We need a complete design for our construction company KELTO CONSTRUCTION based in Auckland New Zealand, we need a logo, website, business card, vehicle design etc..
We are a mid to high-end construction company who work mostly on residential projects and some commercial.

What we want to see in the design;
Professional,
Architectural,
Simple,
Alternative,

We want the design to communicate professionalism, high quality wormanship and and quality service.

Target Market(s)

People looking for a quality building/ construction company

Industry/Entity Type

Construction Company

Contact Information for Business Card

KELTO CONSTRUCTION.co.nz
Lino Verasek
lino@keltoconstruction.example.nz
021 5807 462

Logo Text

KELTO CONSTRUCTION

Number of Pages Required

5+ page

Font styles to use
Sans Serif

Colors

Designer to choose colors to be used in the design.

Requirements
Must have
• Must appear high end, professional, quality, be simple, easy to use, give security to potential clients
Nice to have
• high-quality photos of our recent projects
• about us page
• blog page
• contact us page
• high quality content
Should not have
• should not be hard to use and have too much going on.

```html
<!DOCTYPE html>
<html lang="en">
<head>
<meta charset="utf-8">
<title>Kelto Construction</title>
<link rel="stylesheet" href="https://fonts.googleapis.com/css2?family=Questrial&family=Montserrat:wght@500;600&family=Raleway:wght@300&display=swap">
<style>
:root{
  --ink:#111;
  --white:#fff;
  --muted:#8a8f96;
  --light:#eeeeee;
  --grey-text:#555;
  --navy:#0b1420;
  --navy-2:#16202c;
  --line:#999;
}
*{margin:0;padding:0;box-sizing:border-box}
html,body{width:1200px;height:2284px;overflow:hidden;background:var(--white)}
body{position:relative;font-family:"Questrial",sans-serif;color:var(--ink)}
.abs{position:absolute;white-space:nowrap}
.label{font-family:"Montserrat",sans-serif;font-weight:600;letter-spacing:.5px}

/* hero */
.hero{left:0;top:0;width:1200px;height:519px;
  background:
    radial-gradient(ellipse 260px 70px at 660px 432px,rgba(255,90,40,.85),rgba(200,60,30,0) 100%),
    radial-gradient(ellipse 520px 120px at 600px 420px,rgba(190,80,50,.7),rgba(120,50,40,0) 100%),
    linear-gradient(90deg,rgba(0,0,0,0) 55%,rgba(8,8,10,.8) 62%,rgba(12,12,14,.85) 100%),
    linear-gradient(180deg,#2b2b31 0%,#47423f 30%,#7b6052 55%,#9a5a40 72%,#2a2220 82%,#131315 100%)}
.hero-shade{left:0;top:0;width:1200px;height:519px;background:linear-gradient(180deg,rgba(0,0,0,.35),rgba(0,0,0,0) 20%,rgba(0,0,0,0) 80%,rgba(0,0,0,.4))}
.brand{left:55px;top:26px;font-family:"Montserrat",sans-serif;font-weight:500;font-size:21px;letter-spacing:2px;color:var(--white)}
.nav{top:30px;font-family:"Montserrat",sans-serif;font-weight:500;font-size:14px;letter-spacing:1px;color:var(--white);transform:translateX(-50%)}
.nav.active::after{content:"";position:absolute;left:0;right:0;top:25px;height:1px;background:var(--white)}
.hero-title{left:0;width:1200px;top:232px;text-align:center;font-family:"Raleway",sans-serif;font-weight:300;font-size:52px;letter-spacing:4px;color:var(--white)}
.hero-sub{left:0;width:1200px;top:293px;text-align:center;font-size:15px;color:#e8e8e8}
.hero-btn{left:525px;top:341px;width:150px;height:44px;border:1px solid var(--white);color:var(--white);font-family:"Montserrat",sans-serif;font-weight:500;font-size:11px;letter-spacing:1px;display:flex;align-items:center;justify-content:center}
.dot{top:465px;width:6px;height:6px;border-radius:50%;background:rgba(255,255,255,.45)}
.dot.on{background:var(--white)}

/* sectors */
.sectors{left:0;top:519px;width:1200px;height:357px;background:var(--light)}
.sector{top:571px;width:517px;height:250px}
.sector-res{left:69px;background:
  radial-gradient(ellipse 160px 70px at 330px 150px,rgba(230,150,70,.55),rgba(230,150,70,0)),
  linear-gradient(90deg,rgba(20,30,25,.7) 0%,rgba(20,30,25,0) 20%,rgba(20,30,25,0) 82%,rgba(20,30,25,.7) 100%),
  linear-gradient(180deg,#4e6d8c 0%,#3f5068 40%,#56555a 62%,#4a4038 78%,#222 100%)}
.sector-com{left:612px;background:
  linear-gradient(90deg,rgba(230,205,160,.9) 0%,rgba(220,190,140,.8) 45%,rgba(200,225,235,0) 75%),
  linear-gradient(180deg,rgba(0,0,0,0) 55%,rgba(60,50,45,.6) 100%),
  linear-gradient(180deg,#b9d6e4 0%,#d6e5ea 100%)}
.sector-name{top:788px;font-size:14px;color:var(--white)}

/* projects */
.projects{left:0;top:876px;width:1200px;height:502px;background:radial-gradient(ellipse at 55% 60%,#2a3440 0%,var(--navy-2) 40%,var(--navy) 100%)}
.sec-title{left:0;width:1200px;text-align:center;font-family:"Montserrat",sans-serif;font-weight:500;font-size:18px;letter-spacing:1.5px}
.proj-img{top:1020px;width:244px;height:169px}
.p1{background:linear-gradient(180deg,rgba(0,0,0,0) 55%,rgba(70,60,50,.6)),linear-gradient(90deg,#b8ad98,#8a8478 40%,#a6c4de 75%,#7faad0)}
.p2{background:linear-gradient(180deg,#1a62b8 0%,#3d8ad8 45%,#9bc6ec 62%,#7b7a72 80%,#4a4a48 100%)}
.p3{background:linear-gradient(135deg,#7d97cf 0%,#b9bfcf 35%,#8c8a88 60%,#5d5a58 85%,#c9c32a 100%)}
.p4{background:linear-gradient(180deg,#1f78c8 0%,#4e9ede 50%,#8cc4ef 80%,#b0aaa4 100%)}
.proj-name{top:1213px;font-size:14px;color:var(--white)}
.proj-text{top:1238px;width:228px;font-size:11.5px;line-height:18px;color:var(--muted);white-space:normal}

/* blog */
.blog-img{width:153px;height:131px}
.b1{background:radial-gradient(circle at 75% 65%,#ffd27a,rgba(255,210,120,0) 45%),linear-gradient(135deg,#c88a3a,#7a5a36 55%,#2e2a26)}
.b2{background:linear-gradient(180deg,#6fa6e2 0%,#b8c8d8 40%,#8a8a82 60%,#3e4a34 100%)}
.b3{background:linear-gradient(180deg,#4f9ae0 0%,#8cc0ea 35%,#d8d070 65%,#6a7a3a 100%)}
.b4{background:radial-gradient(circle at 40% 35%,#b8b0a6,rgba(184,176,166,0) 55%),linear-gradient(140deg,#8a8782,#55524d 55%,#2e2b28)}
.date{font-family:"Montserrat",sans-serif;font-weight:600;font-size:11.5px}
.excerpt{width:355px;font-size:15px;line-height:18px;color:var(--grey-text);white-space:normal}
.more{width:104px;height:29px;border:1px solid var(--line);font-family:"Montserrat",sans-serif;font-weight:600;font-size:11px;letter-spacing:.5px;display:flex;align-items:center;justify-content:center}

/* contact */
.contact{left:0;top:1876px;width:1200px;height:326px;background:radial-gradient(ellipse at 30% 100%,#cfcfcf,rgba(207,207,207,0) 60%),linear-gradient(180deg,#e4e4e4,#d8d8d8 60%,#e6e6e6)}
.contact-title{left:99px;top:1920px;font-family:"Montserrat",sans-serif;font-weight:500;font-size:19px;letter-spacing:1px}
.field{background:var(--white);font-size:11px;color:#888;padding:8px 12px}
.submit{left:99px;top:2102px;width:122px;height:29px;background:var(--ink);color:var(--white);font-family:"Montserrat",sans-serif;font-weight:600;font-size:11px;letter-spacing:.5px;display:flex;align-items:center;justify-content:center}
.c-name{left:702px;top:1954px;font-family:"Montserrat",sans-serif;font-weight:500;font-size:19px;letter-spacing:1.5px}
.c-city{left:702px;top:1986px;font-size:13px}
.c-phone{left:702px;top:2027px;font-size:24px;letter-spacing:1.5px}
.c-mail{left:702px;top:2064px;font-size:15px;letter-spacing:.5px}

/* footer */
.foot-brand{left:55px;top:2234px;font-family:"Montserrat",sans-serif;font-weight:500;font-size:21px;letter-spacing:2px}
.copy{right:66px;top:2238px;font-size:12px;color:#222}
</style>
</head>
<body>

<div class="abs hero" role="img" aria-label="City skyline with cranes and a high-rise under construction at sunset"></div>
<div class="abs hero-shade"></div>
<div class="abs brand">KELTO CONSTRUCTION</div>
<div class="abs nav active" style="left:678px">HOME</div>
<div class="abs nav" style="left:778px">ABOUT US</div>
<div class="abs nav" style="left:895px">PROJECTS</div>
<div class="abs nav" style="left:994px">BLOG</div>
<div class="abs nav" style="left:1104px">CONTACT US</div>
<h1 class="abs hero-title">KELTO CONSTRUCTION</h1>
<p class="abs hero-sub">We are a mid to high-end construction company</p>
<div class="abs hero-btn">LEARN MORE</div>
<span class="abs dot on" style="left:570px"></span>
<span class="abs dot" style="left:588px"></span>
<span class="abs dot" style="left:606px"></span>
<span class="abs dot" style="left:623px"></span>

<section class="abs sectors"></section>
<div class="abs sector sector-res" role="img" aria-label="Modern two-storey family home at dusk"></div>
<div class="abs sector sector-com" role="img" aria-label="Apartment building facade with balconies"></div>
<div class="abs sector-name label" style="left:87px">RESIDENTIAL</div>
<div class="abs sector-name label" style="left:634px">COMMERCIAL</div>

<section class="abs projects" role="img" aria-label="Blurred dark building background"></section>
<h2 class="abs sec-title" style="top:953px;color:var(--white)">RECENT PROJECTS</h2>
<div class="abs proj-img p1" style="left:69px" role="img" aria-label="Concrete building frame under construction"></div>
<div class="abs proj-img p2" style="left:341px" role="img" aria-label="Tower cranes over a building site"></div>
<div class="abs proj-img p3" style="left:614px" role="img" aria-label="Scaffolding and a worker in high-visibility vest"></div>
<div class="abs proj-img p4" style="left:886px" role="img" aria-label="Concrete column with steel reinforcement bars"></div>
<div class="abs proj-name label" style="left:68px">PROJECT 1</div>
<div class="abs proj-name label" style="left:342px">PROJECT 2</div>
<div class="abs proj-name label" style="left:614px">PROJECT 3</div>
<div class="abs proj-name label" style="left:891px">PROJECT 4</div>
<p class="abs proj-text" style="left:68px">Sed ut perspiciatis unde omnis iste natus error sit voluptatem accusantium</p>
<p class="abs proj-text" style="left:342px">Sed ut perspiciatis unde omnis iste natus error sit voluptatem accusantium</p>
<p class="abs proj-text" style="left:614px">Sed ut perspiciatis unde omnis iste natus error sit voluptatem accusantium</p>
<p class="abs proj-text" style="left:891px">Sed ut perspiciatis unde omnis iste natus error sit voluptatem accusantium</p>
<svg class="abs" style="left:585px;top:1314px" width="30" height="16" viewBox="0 0 30 16" aria-hidden="true">
  <path d="M6 3 L2 8 L6 13" fill="none" stroke="#9aa0a8" stroke-width="1.5"/>
  <path d="M24 3 L28 8 L24 13" fill="none" stroke="#cfd3d8" stroke-width="1.5"/>
</svg>

<h2 class="abs sec-title" style="top:1437px">BLOG</h2>
<div class="abs blog-img b1" style="left:69px;top:1509px" role="img" aria-label="Excavator on a sunlit building site"></div>
<div class="abs date" style="left:236px;top:1517px">March 19th 2017</div>
<p class="abs excerpt" style="left:236px;top:1540px">Sed ut perspiciatis unde omnis iste natus error sit voluptatem accusantium doloremque</p>
<div class="abs more" style="left:236px;top:1596px">READ MORE</div>

<div class="abs blog-img b2" style="left:612px;top:1509px" role="img" aria-label="Bridge construction with a worker in the foreground"></div>
<div class="abs date" style="left:783px;top:1517px">March 19th 2017</div>
<p class="abs excerpt" style="left:783px;top:1540px">Sed ut perspiciatis unde omnis iste natus error sit voluptatem accusantium doloremque</p>
<div class="abs more" style="left:783px;top:1596px">READ MORE</div>

<div class="abs blog-img b3" style="left:69px;top:1678px" role="img" aria-label="Engineers in hard hats reviewing plans"></div>
<div class="abs date" style="left:236px;top:1686px">March 19th 2017</div>
<p class="abs excerpt" style="left:236px;top:1709px">Sed ut perspiciatis unde omnis iste natus error sit voluptatem accusantium doloremque</p>
<div class="abs more" style="left:236px;top:1765px">READ MORE</div>

<div class="abs blog-img b4" style="left:612px;top:1678px" role="img" aria-label="Gloved hands tying reinforcement steel"></div>
<div class="abs date" style="left:783px;top:1686px">March 19th 2017</div>
<p class="abs excerpt" style="left:783px;top:1709px">Sed ut perspiciatis unde omnis iste natus error sit voluptatem accusantium doloremque</p>
<div class="abs more" style="left:783px;top:1765px">READ MORE</div>

<section class="abs contact" role="img" aria-label="Faint grey background of cranes over a city"></section>
<h2 class="abs contact-title">CONTACT US</h2>
<div class="abs field" style="left:99px;top:1957px;width:239px;height:31px">Name</div>
<div class="abs field" style="left:361px;top:1957px;width:239px;height:31px">E-Mail</div>
<div class="abs field" style="left:99px;top:2009px;width:501px;height:76px">Message</div>
<div class="abs submit">SUBMIT</div>

<svg class="abs" style="left:667px;top:1956px" width="16" height="22" viewBox="0 0 16 22" aria-hidden="true">
  <path d="M8 0 C3.6 0 0 3.4 0 7.8 C0 13 8 22 8 22 C8 22 16 13 16 7.8 C16 3.4 12.4 0 8 0 Z" fill="#111"/>
  <circle cx="8" cy="7.8" r="3" fill="#e0e0e0"/>
</svg>
<div class="abs c-name">KELTO CONSTRUCTION</div>
<div class="abs c-city">Auckland newzealnd</div>
<svg class="abs" style="left:665px;top:2030px" width="20" height="20" viewBox="0 0 24 24" aria-hidden="true">
  <path d="M6.6 10.8c1.4 2.8 3.8 5.2 6.6 6.6l2.2-2.2c.3-.3.7-.4 1-.2 1.1.4 2.3.6 3.6.6.6 0 1 .4 1 1V20c0 .6-.4 1-1 1C10.6 21 3 13.4 3 4c0-.6.4-1 1-1h3.5c.6 0 1 .4 1 1 0 1.3.2 2.5.6 3.6.1.3 0 .7-.2 1L6.6 10.8z" fill="#111"/>
</svg>
<div class="abs c-phone">1-900-555-0142</div>
<svg class="abs" style="left:664px;top:2067px" width="22" height="15" viewBox="0 0 22 15" aria-hidden="true">
  <rect x="0" y="0" width="22" height="15" fill="#111"/>
  <path d="M0 0 L11 8.5 L22 0" fill="none" stroke="#ddd" stroke-width="1.3"/>
</svg>
<div class="abs c-mail">info@keltoconstruction.example.nz</div>

<div class="abs foot-brand">KELTO CONSTRUCTION</div>
<div class="abs copy">© 2018 Company Name |&nbsp; All Rights Reserved</div>

</body>
</html>
```